Verodex business card

Business card for sustainable investment company called "Verodex". Verodex is an exchange platform selling carbon credits between buyers and sellers. Carbon Credits are an environmental commodity for reducing global carbon emissions.

the card should obviously have our logo and the theme should be sustainability/environment mixed with a trading platform.

Contact Information for Business Card

Logo, Name, Title, Phone, Email

Colors
0054AA
0677BA
7BADD7
CADEEF
E8F1F8
0094D4
00A9DD
6FCCEA
C7EBF8
E9F6FB
00AB8E
00BBA5
67D7C9
C6EFE9
E9F9F6
59FF00
82FF00
B8FF75
E3FFCB
F4FFEA

```html
<!DOCTYPE html>
<html lang="en">
<head>
<meta charset="utf-8">
<title>Verodex business card</title>
<link rel="stylesheet" href="https://fonts.googleapis.com/css2?family=Montserrat:wght@600;700&family=Open+Sans:wght@400;600;700&display=swap">
<style>
  :root {
    --navy: #142b50;
    --sky: #6fcfe6;
    --azure: #4a7fc8;
    --accent: #5aa8df;
    --white: #ffffff;
    --backdrop: #e8f1f8;
  }
  * { margin: 0; padding: 0; box-sizing: border-box; }
  html, body { width: 1200px; height: 780px; overflow: hidden; }
  body {
    background: var(--backdrop);
    font-family: "Open Sans", sans-serif;
    display: flex;
    align-items: center;
    justify-content: center;
    gap: 40px;
  }
  .card {
    position: relative;
    width: 540px;
    height: 308px;
    border-radius: 22px;
    overflow: hidden;
    box-shadow: 0 10px 28px rgba(20, 43, 80, 0.25);
  }
  .card-bg { position: absolute; inset: 0; }
  /* back side */
  .brand-block {
    position: absolute;
    left: 30px; top: 70px;
    width: 210px;
    display: flex; flex-direction: column; align-items: center; gap: 14px;
  }
  .brand-dot {
    width: 62px; height: 62px; border-radius: 50%;
    background: var(--accent);
  }
  .brand-name {
    font-family: "Open Sans", sans-serif;
    font-weight: 700; font-size: 34px;
    color: var(--accent); letter-spacing: 1px;
  }
  .divider {
    position: absolute; left: 262px; top: 78px;
    width: 1px; height: 150px;
    background: linear-gradient(var(--white), rgba(255,255,255,0.2));
  }
  .person { position: absolute; left: 286px; top: 96px; color: var(--white); }
  .person-name { font-weight: 700; font-size: 25px; color: var(--accent); line-height: 1.1; }
  .person-title { font-weight: 600; font-size: 15px; margin-top: 2px; }
  .contact-list { list-style: none; margin-top: 12px; }
  .contact-list li {
    display: flex; align-items: center; gap: 7px;
    font-size: 13.5px; line-height: 1.6;
  }
  .contact-icon { width: 13px; height: 13px; flex: none; }
  .address {
    position: absolute; left: 34px; top: 250px;
    color: var(--white); font-size: 12.5px;
  }
  /* front side */
  .wordmark {
    position: absolute; inset: 0;
    display: flex; align-items: center; justify-content: center; gap: 16px;
  }
  .wordmark-dot { width: 40px; height: 40px; border-radius: 50%; background: var(--accent); }
  .wordmark-name {
    font-family: "Open Sans", sans-serif;
    font-weight: 700; font-size: 52px; letter-spacing: 3px;
    color: var(--white); text-transform: uppercase;
  }
</style>
</head>
<body>
  <svg width="0" height="0" style="position:absolute">
    <defs>
      <linearGradient id="edge-glow" x1="0" y1="0" x2="1" y2="1">
        <stop offset="0" stop-color="#4a7fc8"/>
        <stop offset="0.5" stop-color="#6fcfe6"/>
        <stop offset="1" stop-color="#4a7fc8"/>
      </linearGradient>
    </defs>
  </svg>

  <article class="card card-back">
    <svg class="card-bg" viewBox="0 0 540 308" preserveAspectRatio="none">
      <rect width="540" height="308" fill="url(#edge-glow)"/>
      <path d="M0,90 C70,35 190,12 330,0 L540,0 L540,222 C465,280 345,300 215,308 L0,308 Z" fill="#142b50"/>
    </svg>
    <div class="brand-block">
      <span class="brand-dot"></span>
      <span class="brand-name">Verodex</span>
    </div>
    <span class="divider"></span>
    <div class="person">
      <h1 class="person-name">Alena Marvek</h1>
      <p class="person-title">Managing Director</p>
      <ul class="contact-list">
        <li>
          <svg class="contact-icon" viewBox="0 0 16 16"><circle cx="8" cy="8" r="8" fill="#5aa8df"/><path d="M5 4.2l1.6-.4 1 2.2-1 .8c.5 1.1 1.3 1.9 2.4 2.4l.8-1 2.2 1-.4 1.6c-3.6.3-6.9-3-6.6-6.6z" fill="#fff"/></svg>
          (940) 555-0163
        </li>
        <li>
          <svg class="contact-icon" viewBox="0 0 16 16"><circle cx="8" cy="8" r="8" fill="#5aa8df"/><rect x="4" y="5" width="8" height="6" rx="1" fill="#fff"/><path d="M4 5.5l4 3 4-3" stroke="#5aa8df" stroke-width="1" fill="none"/></svg>
          hello@verodex.net
        </li>
        <li>
          <svg class="contact-icon" viewBox="0 0 16 16"><circle cx="8" cy="8" r="8" fill="#5aa8df"/><circle cx="8" cy="8" r="4" fill="none" stroke="#fff" stroke-width="1.1"/><path d="M4 8h8M8 4c-1.6 2.4-1.6 5.6 0 8M8 4c1.6 2.4 1.6 5.6 0 8" stroke="#fff" stroke-width="0.9" fill="none"/></svg>
          www.verodex.net
        </li>
      </ul>
    </div>
    <p class="address">480 Lindenhall Ave. Suite 310 Denton, TX 76201</p>
  </article>

  <article class="card card-front">
    <svg class="card-bg" viewBox="0 0 540 308" preserveAspectRatio="none">
      <rect width="540" height="308" fill="url(#edge-glow)"/>
      <path d="M0,90 C70,35 190,12 330,0 L540,0 L540,222 C465,280 345,300 215,308 L0,308 Z" fill="#142b50"/>
    </svg>
    <div class="wordmark">
      <span class="wordmark-dot"></span>
      <span class="wordmark-name">Verodex</span>
    </div>
  </article>
</body>
</html>
```